Tall ridge firewood

It a new firewood outlet in Jindabyne nsw that will only sell top hardwood firewood (ironbark , red gum, grey gum, an box mix. I would like to see a web page the we can do order online payment for delivery. It will all so need to have photos of the firewood. I all so have logo for tall ridge firewood
Must have a modem look but easy to use I would like to see a black back ground of some sort.

Here are some other firewood web pages for ideas and firewood info
http://www.example-logpile.com.au
http://www.example-stackwood.com.au
http://www.example-splitlog.com.au
http://www.example-kendaltimber.com.au/firewood

Industry/Entity Type

Firewood

```html
<!DOCTYPE html>
<html lang="en">
<head>
<meta charset="utf-8">
<title>Tall Ridge Firewood</title>
<link href="https://fonts.googleapis.com/css2?family=Anton&family=Montserrat:wght@400;600;700&display=swap" rel="stylesheet">
<style>
:root{
  --blue:#1f6db5;
  --navy:#1c1d2c;
  --tan:#c89b6c;
  --grey-bg:#efefef;
  --text:#2a2a2a;
  --muted:#8a8a8a;
  --red:#c8161d;
  --footer:#141010;
  --white:#ffffff;
}
*{box-sizing:border-box;margin:0;padding:0}
html,body{width:943px;height:1200px;overflow:hidden}
body{position:relative;font-family:'Montserrat',sans-serif;color:var(--text);background:var(--white)}
.display{font-family:'Anton',sans-serif;font-weight:400;text-transform:uppercase}
.abs{position:absolute}
.nowrap{white-space:nowrap}

.hero{left:0;top:0;width:943px;height:387px;background:linear-gradient(120deg,#3a2414 0%,#7a4d2c 35%,#5c3a22 60%,#2b1a0e 100%)}
.hero-figure{left:480px;top:50px;width:330px;height:337px;border-radius:40% 40% 0 0;background:linear-gradient(180deg,rgba(36,102,180,.55),rgba(20,60,110,.6))}

.topbar{left:0;top:26px;width:943px;height:42px;background:var(--blue)}
.brand{left:24px;top:27px;color:var(--white);font-size:36px;line-height:40px;white-space:nowrap}
.tagline{left:25px;top:73px;color:var(--white);font-size:9px;letter-spacing:1px;font-weight:600;white-space:nowrap}
.nav{left:374px;top:26px;height:42px;display:flex}
.nav a{display:flex;align-items:center;justify-content:center;height:42px;color:var(--white);text-decoration:none;font-family:'Anton',sans-serif;font-size:12.5px;text-transform:uppercase;white-space:nowrap;border-left:1px solid rgba(255,255,255,.18)}
.nav a.active{background:var(--navy)}
.nav .phone{font-size:17px;gap:6px;justify-content:flex-start;padding-left:14px}

.headline{left:140px;top:156px;color:var(--white);font-size:45px;line-height:42px;white-space:nowrap}
.slide-arrow{top:191px;width:48px;height:67px;background:rgba(255,255,255,.25);border:1px solid rgba(255,255,255,.5);display:flex;align-items:center;justify-content:center}

.welcome{left:0;top:387px;width:943px;height:391px;background:var(--grey-bg)}
.welcome h2{position:absolute;left:140px;top:27px;font-size:22px;color:var(--navy);white-space:nowrap}
.welcome h2 span{color:var(--blue)}
.video{left:139px;top:81px;width:182px;height:145px;background:linear-gradient(180deg,#6d6d6d,#3b2a20 45%,#b8421a 60%,#2a2320)}
.play{left:69px;top:51px}
.lead{left:335px;top:78px;width:243px;font-size:11.2px;line-height:15.5px;text-align:justify;color:var(--text)}
.body-copy{left:139px;top:168px;width:439px;font-size:9.5px;line-height:13.2px;text-align:justify;color:var(--muted)}
.body-copy .indent{display:block;padding-left:196px}

.order{left:611px;top:338px;width:192px;height:388px;background:var(--tan);box-shadow:0 2px 6px rgba(0,0,0,.15)}
.order-head{height:47px;background:var(--blue);color:var(--white);font-size:20px;display:flex;align-items:center;justify-content:center}
.order-intro{margin:14px 22px 0;font-size:8px;line-height:11px;color:#3a2a1c}
.order-intro b{color:var(--navy)}
.field{margin:11px 22px 0;height:20px;background:var(--white);border:1px solid #e3d3c2;font-size:7.5px;color:#777;display:flex;align-items:center;padding-left:8px;position:relative}
.field + .field{margin-top:4px}
.field .req{color:var(--red);margin-left:2px}
.field.select::after{content:"";position:absolute;right:0;top:0;width:9px;height:18px;background:var(--navy)}
.next{margin:13px 22px 0;height:37px;background:var(--blue);color:var(--white);font-size:23px;display:flex;align-items:center;justify-content:center;gap:9px}

.products{left:0;top:778px;width:943px;height:254px;background:#f8f8f8;border-top:1px solid #e2e2e2}
.products h2{position:absolute;left:0;width:943px;top:22px;text-align:center;font-size:22px;color:var(--blue)}
.products h2 span{color:var(--navy)}
.card{top:79px;width:159px;text-align:center}
.card .photo{height:94px}
.card .name{margin-top:10px;font-size:10.5px;color:var(--text)}
.card .note{font-size:6.5px;color:var(--muted);margin-top:1px}
.card .price{font-size:11px;font-weight:700;color:var(--red)}
.round-arrow{top:119px;width:20px;height:20px;border-radius:50%;background:#8c8c8c;display:flex;align-items:center;justify-content:center}

.footer{left:0;top:1032px;width:943px;height:168px;background:radial-gradient(circle at 50% 40%,#3b2416 0%,var(--footer) 70%)}
.footer h3{font-size:13px;color:var(--blue);position:absolute;top:40px;white-space:nowrap}
.f-nav{left:140px;top:72px;list-style:none}
.f-nav li{font-size:7.5px;font-weight:700;color:var(--white);line-height:15.5px;text-transform:uppercase}
.f-contact{left:236px;top:70px;font-size:8px;line-height:12px;color:#a9a9a9;width:140px}
.f-contact a{color:var(--blue);text-decoration:none}
.f-hours{left:580px;top:70px;width:115px}
.f-hours p{font-size:7px;font-weight:700;color:var(--white);padding:4px 2px;border-bottom:1px solid rgba(255,255,255,.15);white-space:nowrap}
.f-lines{left:707px;top:70px;font-size:13px;line-height:17px;color:var(--white)}
.f-logo{left:381px;top:26px;width:180px;text-align:center}
.f-mark{width:58px;height:58px;margin:0 auto;border-radius:50%;background:linear-gradient(180deg,#2f6cb3,#20324d)}
.f-name{color:var(--white);font-size:15px;margin-top:4px;white-space:nowrap}
.f-tag{font-size:5px;color:#d0d0d0;margin-top:2px;letter-spacing:.3px;white-space:nowrap}
.f-copy{font-size:7px;color:#bbbbbb;margin-top:12px}
</style>
</head>
<body>

<header>
  <div class="abs hero" role="img" aria-label="Background photo of stacked hardwood logs"></div>
  <div class="abs hero-figure" role="img" aria-label="Illustrated woodcutter mascot carrying an axe"></div>
  <div class="abs topbar"></div>
  <div class="abs brand display">Tall Ridge Firewood</div>
  <div class="abs tagline">WOOD THAT GETS YOU HOT AND LAST ALL NIGHT LONG</div>
  <nav class="abs nav">
    <a class="active" href="#" style="width:50px">Home</a>
    <a href="#" style="width:71px">About Us</a>
    <a href="#" style="width:78px">Products</a>
    <a href="#" style="width:91px">Order Online</a>
    <a href="#" style="width:38px">FAQ</a>
    <a href="#" style="width:90px">Contact Us</a>
    <a class="phone" href="#" style="width:151px">
      <svg width="11" height="17" viewBox="0 0 11 17"><rect x="1" y="1" width="9" height="15" rx="1.5" fill="none" stroke="#fff" stroke-width="1.5"/><circle cx="5.5" cy="13.3" r="1" fill="#fff"/></svg>
      0400 555 018
    </a>
  </nav>
  <h1 class="abs headline display">Delivering top<br>quality seasoned<br>hardwood all<br>year round</h1>
  <div class="abs slide-arrow" style="left:0">
    <svg width="14" height="22" viewBox="0 0 14 22"><path d="M11 2 L3 11 L11 20" fill="none" stroke="#fff" stroke-width="4"/></svg>
  </div>
  <div class="abs slide-arrow" style="left:893px">
    <svg width="14" height="22" viewBox="0 0 14 22"><path d="M3 2 L11 11 L3 20" fill="none" stroke="#fff" stroke-width="4"/></svg>
  </div>
</header>

<section class="abs welcome">
  <h2 class="display">Welcome <span>to our new online store</span></h2>
  <div class="abs video" role="img" aria-label="Video still of a fire burning in a wood heater">
    <svg class="abs play" width="44" height="44" viewBox="0 0 44 44"><circle cx="22" cy="22" r="20" fill="#1f6db5" stroke="#fff" stroke-width="3"/><path d="M17 13 L31 22 L17 31Z" fill="#fff"/></svg>
  </div>
  <p class="abs lead">This is Studio's version of Lorem Ipsum. Proin gravida nibh vel velit auctor aliquet. Aenean sollicitudin, lorem quis bibendum auctor, nisi elit consequat ipsum, nec sagittis sem nibh id elit.</p>
  <p class="abs body-copy"><span class="indent">This is Studio's version of Lorem Ipsum. Proin gravida nibh vel velit auctor aliquet. Aenean sollicitudin, lorem quis bibendum auctor, nisi elit consequat ipsum, nec sagittis sem nibh id elit. Duis sed odio sit amet nibh vulputate cursus a sit amet</span>tincidunt auctor a ornare odio. Sed non mauris vitae erat consequat auctor eu in elit. Class aptent taciti sociosqu ad litora torquent per conubia nostra, per inceptos himenaeos. Mauris in erat justo. Nullam ac urna eu felis dapibus condimentum sit amet a augue. Sed non neque elit. Sed ut imperdiet nisi. Proin condimentum fermentum nunc. Etiam pharetra, erat sed fermentum feugiat, velit mauris egestas quam, ut aliquam massa nisl quis neque. Suspendisse in orci enim. This is Studio's version of Lorem Ipsum. Proin gravida nibh vel velit auctor aliquet. Aenean sollicitudin, lorem quis bibendum auctor.</p>
</section>

<aside class="abs order">
  <div class="order-head display">Order Firewood</div>
  <p class="order-intro">Fill out the form below to order your firewood delivery. Deliveries are usually between <b>4:00PM &amp; 9:00PM</b> Can take up to 2 weeks to deliver (especially in the off session)</p>
  <div class="field">Email<span class="req">*</span></div>
  <div class="field">Phone</div>
  <div class="field">Address<span class="req">*</span></div>
  <div class="field">Zip Code/City<span class="req">*</span></div>
  <div class="field">Gate Code (if needed)</div>
  <div class="field select">Firewood Type</div>
  <div class="field select">Order Size</div>
  <div class="field select">Kindling</div>
  <div class="next display">Next
    <svg width="18" height="18" viewBox="0 0 18 18"><circle cx="9" cy="9" r="8.5" fill="#fff"/><path d="M4 9 H12 M9 5 L13 9 L9 13" fill="none" stroke="#1f6db5" stroke-width="2.4"/></svg>
  </div>
</aside>

<section class="abs products">
  <h2 class="display">New products for <span>February</span></h2>
  <div class="abs round-arrow" style="left:102px">
    <svg width="8" height="10" viewBox="0 0 8 10"><path d="M6 1 L2 5 L6 9" fill="none" stroke="#fff" stroke-width="2"/></svg>
  </div>
  <div class="abs card" style="left:139px">
    <div class="photo" role="img" aria-label="Photo of a stack of mixed split hardwood" style="background:linear-gradient(135deg,#9a9a9a,#c87a3e 55%,#6e4a2c)"></div>
    <div class="name">MIXED HARDWOOD</div><div class="note">PICK-UP TRUCK LOAD</div><div class="price">$25.00</div>
  </div>
  <div class="abs card" style="left:307px">
    <div class="photo" role="img" aria-label="Photo of round unsplit log ends" style="background:linear-gradient(135deg,#6b5440,#b89a78 50%,#4e3c2c)"></div>
    <div class="name">UNSPLIT WOOD</div><div class="note">STARTING AT</div><div class="price">$1.00 A LOG</div>
  </div>
  <div class="abs card" style="left:475px">
    <div class="photo" role="img" aria-label="Photo of a bunch of kindling sticks" style="background:linear-gradient(135deg,#e0a56a,#b46a36 55%,#d89860)"></div>
    <div class="name">BUNCH OF KINDLING</div><div class="note">1 FOR</div><div class="price">$10.00</div>
  </div>
  <div class="abs card" style="left:644px">
    <div class="photo" role="img" aria-label="Photo of plain wood mulch chips" style="background:linear-gradient(135deg,#a8a090,#8a7c66 50%,#b6ae9c)"></div>
    <div class="name">PLAIN WOOD MULCH</div><div class="note">PICK-UP TRUCK LOAD</div><div class="price">$25.00</div>
  </div>
  <div class="abs round-arrow" style="left:817px">
    <svg width="8" height="10" viewBox="0 0 8 10"><path d="M2 1 L6 5 L2 9" fill="none" stroke="#fff" stroke-width="2"/></svg>
  </div>
</section>

<footer class="abs footer">
  <h3 class="display" style="left:140px">Navigation</h3>
  <ul class="abs f-nav">
    <li>Home</li><li>About Us</li><li>Our Products</li><li>Firewood</li><li>Fencing</li>
  </ul>
  <h3 class="display" style="left:236px">Contact Us</h3>
  <p class="abs f-contact">Tall Ridge Firewood LTD.<br>14 Snowy Lane Jindabyne,<br>NSW 2627<br><br><a href="#">contact@tallridgefirewood.com</a></p>
  <div class="abs f-logo">
    <div class="f-mark" role="img" aria-label="Woodcutter mascot illustration"></div>
    <div class="f-name display">Tall Ridge Firewood</div>
    <div class="f-tag">WOOD THAT GETS YOU HOT AND LAST ALL NIGHT LONG</div>
    <div class="f-copy">Copyrights © 2014, All rights Reserved</div>
  </div>
  <h3 class="display" style="left:580px">Hours:</h3>
  <div class="abs f-hours">
    <p>MON-THUR 8:00AM-8:00PM</p><p>FRIDAY 8:00AM-4:00PM</p><p>SATURDAY CLOSED ALL DAY</p><p style="border:0">SUNDAY 8:00AM-7:00PM</p>
  </div>
  <h3 class="display" style="left:707px">Enquiry Hotline</h3>
  <p class="abs f-lines">02 5550 1147<br>0400 555 392</p>
</footer>

</body>
</html>
```